The Copperline Collective's website for high impact furniture promotions

I am looking for a simple website. we are a promotional company that runs events for furniture stores to increase sales for short periods of time. i would like the website to have about 4 areas to explain our company. I would like it to be simple and user friendly. I would like a link to chatterbook and a contact section. I am attaching our logo that i would like somewhere large or possibly in the backround. I am open to different color schemes. I would like to convey fast paced, modern, reliable. I am open to all different styles and look forward to seeing whats out there. we are looking for a quick turn around, so if we see one that we like quick, we will pick that one thanks
Reason: looking for some really creative designs and want to give a fair amount of time to produce
Target Market(s)
Retail Furniture store owners
Industry/Entity Type
It Company
Number of Pages Required
1 page
Colors
Designer to choose colors to be used in the design.
Look and feel

```html
<!DOCTYPE html>
<html lang="en">
<head>
<meta charset="utf-8">
<title>The Copperline Collective</title>
<link href="https://fonts.googleapis.com/css2?family=Open+Sans:ital,wght@0,400;0,600;0,700;1,400&family=Great+Vibes&display=swap" rel="stylesheet">
<style>
:root{
  --bronze:#c49a6c;
  --bronze-dark:#a97f52;
  --ink:#2b2b2b;
  --muted:#6d6d6d;
  --dark:#141210;
  --dark-2:#1d1a17;
  --white:#ffffff;
  --line:#d9d9d9;
  --star:#f2b01e;
}
*{box-sizing:border-box;margin:0;padding:0}
html,body{width:1200px;height:3516px;overflow:hidden}
body{font-family:"Open Sans",Arial,sans-serif;color:var(--ink);background:var(--white);position:relative}
section,footer,header{position:absolute;left:0;width:1200px}
.abs{position:absolute}
.btn{position:absolute;background:var(--bronze);color:var(--white);display:flex;align-items:center;justify-content:center;font-weight:600}

/* hero */
.hero{top:0;height:640px;clip-path:polygon(0 0,1200px 0,1200px 551px,0 638px);overflow:hidden}
.hero-bg{position:absolute;inset:0;background:linear-gradient(135deg,#3a302a 0%,#231d19 45%,#3b2a24 70%,#1c1916 100%)}
.hero-bg::after{content:"";position:absolute;inset:0;background:rgba(0,0,0,.35)}
.brand{position:absolute;left:120px;top:12px;width:150px;text-align:center;color:var(--bronze)}
.brand-mark{width:52px;height:52px;border-radius:50%;background:var(--bronze);margin:0 auto 6px}
.brand-name{font-size:15px;font-weight:600;color:var(--bronze);line-height:1.2}
.call{position:absolute;left:740px;top:30px;display:flex;align-items:center;gap:12px;color:var(--white)}
.call-icon{width:38px;height:38px;border-radius:50%;background:var(--bronze);display:flex;align-items:center;justify-content:center}
.call small{display:block;font-size:12px;font-weight:700}
.call strong{font-size:22px;font-weight:700}
.quote-btn{left:960px;top:35px;width:153px;height:36px;font-size:13px;text-transform:uppercase}
.nav{position:absolute;left:476px;top:86px;width:637px;height:42px;background:rgba(0,0,0,.75);display:flex;align-items:center}
.nav a{color:var(--white);text-decoration:none;font-size:14px;padding:0 24px;height:42px;display:flex;align-items:center}
.nav a.active{background:var(--bronze);padding:0 32px}
.hero-title{position:absolute;top:250px;width:1200px;text-align:center;font-family:"Great Vibes",cursive;color:var(--white);font-size:82px}
.read-btn{left:520px;top:374px;width:160px;height:53px;font-size:20px;font-weight:400;color:#1d1a17}
.dots{position:absolute;display:flex;gap:6px}
.dots i{width:14px;height:14px;border-radius:50%;border:2px solid var(--white)}
.dots i.on{background:var(--bronze);border-color:var(--bronze)}

/* about */
.about{top:640px;height:480px}
.about h2{position:absolute;left:87px;top:72px;font-size:38px;font-weight:400;color:var(--bronze)}
.about p{position:absolute;left:87px;width:520px;font-size:13.5px;line-height:1.65;color:var(--muted)}
.learn-btn{left:87px;top:367px;width:118px;height:34px;font-size:13px}
.video{position:absolute;left:652px;top:75px;width:461px;height:288px;background:linear-gradient(160deg,#eef0f2 0%,#d8dde1 55%,#f0a84a 100%);box-shadow:0 18px 20px -10px rgba(0,0,0,.35)}
.play{position:absolute;left:200px;top:115px;width:60px;height:60px;border-radius:50%;background:rgba(60,60,60,.8);border:3px solid var(--white)}

/* projects */
.projects{top:1120px;height:685px;overflow:hidden}
.band-bg{position:absolute;inset:0}
.projects .band-bg{background:linear-gradient(180deg,#2a221d,#3a2b23 50%,#241c17)}
.band-bg::after{content:"";position:absolute;inset:0;background:rgba(0,0,0,.55)}
.section-title{position:absolute;width:1200px;text-align:center;font-size:34px;font-weight:400}
.projects .section-title{top:70px;color:var(--white)}
.project{position:absolute;top:153px;width:239px;color:var(--white)}
.project .photo{height:208px;border:4px solid var(--white)}
.project h3{font-size:16px;font-weight:600;margin-top:30px}
.project p{font-size:12px;line-height:1.55;margin-top:14px;color:#ddd}
.project a{display:block;font-size:11px;color:#ddd;margin-top:24px}

/* events */
.events{top:1805px;height:593px}
.events .section-title{top:82px;color:var(--bronze)}
.ev-arrows{position:absolute;left:1053px;top:105px;display:flex;gap:6px}
.ev-arrows span{width:24px;height:24px;border:1px solid #bbb;display:flex;align-items:center;justify-content:center}
.event{position:absolute;top:185px;width:328px}
.event .photo{height:178px;border:4px solid var(--white);box-shadow:0 0 0 1px var(--line)}
.event h3{font-size:15px;font-weight:600;margin-top:20px;color:var(--ink)}
.event time{display:block;font-size:11px;margin-top:6px}
.event p{font-size:11.5px;line-height:1.65;margin-top:10px;color:var(--muted)}
.event a{display:block;font-size:11px;font-weight:700;color:var(--ink);margin-top:8px}

/* testimonials */
.clients{top:2398px;height:459px;overflow:hidden}
.clients .band-bg{background:linear-gradient(90deg,#1d1816,#3e2a26 50%,#1c1715)}
.clients .section-title{top:82px;color:var(--white)}
.tcard{position:absolute;top:185px;width:333px;height:171px;border:1px solid rgba(255,255,255,.55);color:var(--white)}
.tcard .qmark{position:absolute;left:-8px;top:-14px;width:34px;height:34px;border-radius:50%;background:var(--white);display:flex;align-items:center;justify-content:center}
.tcard p{position:absolute;left:16px;top:30px;right:16px;font-size:12px;font-style:italic;line-height:1.85}
.avatar{position:absolute;left:40px;top:118px;width:64px;height:64px;border-radius:50%;background:linear-gradient(#c9a98a,#7a5a44);border:3px solid var(--white)}
.tcard .who{position:absolute;left:155px;top:124px;font-size:12px;font-weight:700}
.stars{position:absolute;left:161px;top:144px;display:flex;gap:4px}
.side-arrow{position:absolute;top:258px}

/* partners */
.partners{top:2857px;height:221px}
.badge{position:absolute;top:56px;width:195px;height:111px;border:1px solid var(--line);display:flex;align-items:center;justify-content:center}
.badge span{width:90px;height:40px;border-radius:20px;background:#8a8a8a}

/* footer */
.footer{top:3078px;height:438px;background:var(--dark);color:#cfcfcf}
.footer h4{position:absolute;top:75px;font-size:15px;font-weight:400;color:var(--white);text-transform:uppercase;padding-bottom:8px;border-bottom:1px solid #555}
.f-item{position:absolute;left:90px;display:flex;gap:24px;font-size:12.5px;line-height:1.6}
.f-item svg{flex:none;margin-top:3px}
.social{position:absolute;left:90px;top:262px;font-size:13px;font-weight:600;color:var(--white)}
.field{position:absolute;left:483px;width:240px;height:36px;border:1px solid #777;font-size:12px;color:#aaa;padding:10px 14px}
.send{left:483px;top:292px;width:98px;height:32px;font-size:12px;color:#1d1a17;font-weight:400}
.links{position:absolute;left:845px;top:112px;list-style:none;font-size:12.5px;line-height:2.03}
.links li::before{content:">>";margin-right:22px}
.copy{position:absolute;top:395px;width:1200px;text-align:center;font-size:12px;color:#bbb}
.copy-line{position:absolute;top:375px;left:0;width:1200px;border-top:1px solid #2e2a27}
</style>
</head>
<body>

<header class="hero">
  <div class="hero-bg" role="img" aria-label="Photo of a furniture showroom filled with upholstered chairs"></div>
  <div class="brand">
    <div class="brand-mark"></div>
    <div class="brand-name">The Copperline Collective</div>
  </div>
  <div class="call">
    <span class="call-icon"><svg width="18" height="18" viewBox="0 0 24 24"><path fill="#fff" d="M6.6 10.8a15.1 15.1 0 0 0 6.6 6.6l2.2-2.2c.3-.3.7-.4 1-.2 1.1.4 2.3.6 3.6.6.6 0 1 .4 1 1V20c0 .6-.4 1-1 1A17 17 0 0 1 3 4c0-.6.4-1 1-1h3.5c.6 0 1 .4 1 1 0 1.3.2 2.5.6 3.6.1.3 0 .7-.2 1z"/></svg></span>
    <div><small>CALL US NOW :</small><strong>+408-555-0142</strong></div>
  </div>
  <div class="btn quote-btn">Request a Quote</div>
  <nav class="nav">
    <a class="active">Home</a><a>About Us</a><a>Features</a><a>Services</a><a>Events</a><a>Contact Us</a>
  </nav>
  <h1 class="hero-title">Welcome to Copperline Collective</h1>
  <div class="btn read-btn">Read More</div>
  <div class="dots" style="left:555px;top:508px"><i></i><i></i><i class="on"></i><i></i><i></i></div>
</header>

<section class="about">
  <h2>About Copperline Collective</h2>
  <p style="top:146px">Sed ut perspiciatis unde omnis iste natus error sit voluptatem accusantium doloremque laudantium, totam rem aperiam, eaque ipsa quae ab illo inventore veritatis et quasi architecto beatae vitae dicta sunt explicabo. Nemo enim ipsam voluptatem quia voluptas sit aspernatur aut odit aut fugit, sed quia consequuntur magni dolores eos qui ratione voluptatem sequi nesciunt.</p>
  <p style="top:266px">Neque porro quisquam est, qui dolorem ipsum quia dolor sit amet, consectetur, adipisci velit, sed quia non numquam eius modi tempora incidunt ut labore et dolore magnam aliquam quaerat voluptatem.</p>
  <div class="btn learn-btn">Learn More &rsaquo;</div>
  <div class="video" role="img" aria-label="Video preview of an exhibition stand with branded panels">
    <div class="play"><svg width="54" height="54" viewBox="0 0 54 54"><path fill="#fff" d="M21 16l17 11-17 11z"/></svg></div>
  </div>
</section>

<section class="projects">
  <div class="band-bg" role="img" aria-label="Photo of a furniture warehouse interior"></div>
  <h2 class="section-title">Our Projects</h2>
  <div class="project" style="left:61px"><div class="photo" role="img" aria-label="Photo of a retail store with a sale display" style="background:linear-gradient(160deg,#4d8c8a,#b44a4a 70%,#e0c7b0)"></div><h3>The standard Lorem</h3><p>Sed ut perspiciatis unde omnis iste natus error sit voluptatem accusantium dolo-remque laudantium...</p><a>More &rsaquo;</a></div>
  <div class="project" style="left:324px"><div class="photo" role="img" aria-label="Photo of a blank promotional banner stand" style="background:linear-gradient(160deg,#f0d8d8,#f7f2ee 50%,#d8c4b6)"></div><h3>The standard Lorem</h3><p>Sed ut perspiciatis unde omnis iste natus error sit voluptatem accusantium dolo-remque laudantium...</p><a>More &rsaquo;</a></div>
  <div class="project" style="left:588px"><div class="photo" role="img" aria-label="Photo of red sofas in a showroom" style="background:linear-gradient(180deg,#8a7c70,#b33a32 55%,#3a3d52)"></div><h3>The standard Lorem</h3><p>Sed ut perspiciatis unde omnis iste natus error sit voluptatem accusantium dolo-remque laudantium...</p><a>More &rsaquo;</a></div>
  <div class="project" style="left:851px"><div class="photo" role="img" aria-label="Photo of a busy furniture store floor" style="background:linear-gradient(160deg,#c9b49a,#8a5a3a 55%,#d8cfc4)"></div><h3>The standard Lorem</h3><p>Sed ut perspiciatis unde omnis iste natus error sit voluptatem accusantium dolo-remque laudantium...</p><a>More &rsaquo;</a></div>
  <div class="dots" style="left:570px;top:593px"><i class="on"></i><i></i><i></i></div>
</section>

<section class="events">
  <h2 class="section-title">Upcoming Events</h2>
  <div class="ev-arrows">
    <span><svg width="8" height="12" viewBox="0 0 8 12"><path d="M6 1L1 6l5 5" stroke="#777" fill="none"/></svg></span>
    <span><svg width="8" height="12" viewBox="0 0 8 12"><path d="M2 1l5 5-5 5" stroke="#777" fill="none"/></svg></span>
  </div>
  <article class="event" style="left:87px"><div class="photo" role="img" aria-label="Photo of a sofa showroom" style="background:linear-gradient(180deg,#d9d4c8,#b89c7a 60%,#efe8dd)"></div><h3>De Finibus Bonorum et Malorum", written</h3><time>24 July, 2017</time><p>Lorem ipsum dolor sit amet, consectetur adipiscing elit, sed do eiusmod tempor incididunt ut labore et dolore magna aliqua. Ut enim ad minim veniam...</p><a>More</a></article>
  <article class="event" style="left:436px"><div class="photo" role="img" aria-label="Photo of shoppers choosing furniture" style="background:linear-gradient(160deg,#9fb8c4,#e3c46a 55%,#4c6f9a)"></div><h3>De Finibus Bonorum et Malorum BC</h3><time>24 July, 2017</time><p>Lorem ipsum dolor sit amet, consectetur adipiscing elit, sed do eiusmod tempor incididunt ut labore et dolore magna aliqua. Ut enim ad minim veniam...</p><a>More</a></article>
  <article class="event" style="left:786px"><div class="photo" role="img" aria-label="Photo of a large store aisle with customers" style="background:linear-gradient(180deg,#c7ccd2,#e8e6e2 55%,#9ea4ab)"></div><h3>De Finibus Bonorum et Malorum BC</h3><time>23 July, 2017</time><p>Lorem ipsum dolor sit amet, consectetur adipiscing elit, sed do eiusmod tempor incididunt ut labore et dolore magna aliqua. Ut enim ad minim veniam...</p><a>More</a></article>
</section>

<section class="clients">
  <div class="band-bg" role="img" aria-label="Photo of a customer seated on a sofa in a showroom"></div>
  <h2 class="section-title">Our Clients Says</h2>
  <svg class="side-arrow" style="left:38px" width="12" height="20" viewBox="0 0 12 20"><path d="M10 2L2 10l8 8" stroke="#fff" stroke-width="2" fill="none"/></svg>
  <svg class="side-arrow" style="left:1152px" width="12" height="20" viewBox="0 0 12 20"><path d="M2 2l8 8-8 8" stroke="#fff" stroke-width="2" fill="none"/></svg>
  <div class="tcard" style="left:94px">
    <span class="qmark"><svg width="16" height="14" viewBox="0 0 16 14"><path fill="#222" d="M0 14V7l4-7h3L5 6h2v8zm9 0V7l4-7h3l-2 6h2v8z"/></svg></span>
    <p>Lorem Ipsum is simply dummy text of the printing and typesetting industry. Lorem Ipsum has been the indus-try's standard dummy..</p>
    <div class="avatar" role="img" aria-label="Client portrait"></div>
    <div class="who">Marla K Penrose</div>
    <div class="stars"><svg width="76" height="13" viewBox="0 0 76 13"><g fill="#f2b01e"><path id="s" d="M6.5 0l1.9 4.2 4.6.4-3.5 3 1.1 4.5-4.1-2.4-4.1 2.4 1.1-4.5-3.5-3 4.6-.4z"/><use href="#s" x="16"/><use href="#s" x="32"/><use href="#s" x="48"/><use href="#s" x="63"/></g></svg></div>
  </div>
  <div class="tcard" style="left:441px">
    <span class="qmark"><svg width="16" height="14" viewBox="0 0 16 14"><path fill="#222" d="M0 14V7l4-7h3L5 6h2v8zm9 0V7l4-7h3l-2 6h2v8z"/></svg></span>
    <p>Lorem Ipsum is simply dummy text of the printing and typesetting industry. Lorem Ipsum has been the indus-try's standard dummy..</p>
    <div class="avatar" role="img" aria-label="Client portrait"></div>
    <div class="who">Irene L Whitcombe</div>
    <div class="stars"><svg width="76" height="13" viewBox="0 0 76 13"><g fill="#f2b01e"><use href="#s"/><use href="#s" x="16"/><use href="#s" x="32"/><use href="#s" x="48"/><use href="#s" x="63"/></g></svg></div>
  </div>
  <div class="tcard" style="left:783px">
    <span class="qmark"><svg width="16" height="14" viewBox="0 0 16 14"><path fill="#222" d="M0 14V7l4-7h3L5 6h2v8zm9 0V7l4-7h3l-2 6h2v8z"/></svg></span>
    <p>Lorem Ipsum is simply dummy text of the printing and typesetting industry. Lorem Ipsum has been the indus-try's standard dummy..</p>
    <div class="avatar" role="img" aria-label="Client portrait"></div>
    <div class="who">Delia R Ashgrove</div>
    <div class="stars"><svg width="76" height="13" viewBox="0 0 76 13"><g fill="#f2b01e"><use href="#s"/><use href="#s" x="16"/><use href="#s" x="32"/><use href="#s" x="48"/><use href="#s" x="63"/></g></svg></div>
  </div>
</section>

<section class="partners">
  <div class="badge" style="left:87px"><span></span></div>
  <div class="badge" style="left:295px"><span></span></div>
  <div class="badge" style="left:502px"><span></span></div>
  <div class="badge" style="left:710px"><span></span></div>
  <div class="badge" style="left:917px"><span></span></div>
</section>

<footer class="footer">
  <h4 style="left:90px;width:230px">Contact Us</h4>
  <div class="f-item" style="top:118px"><svg width="10" height="14" viewBox="0 0 10 14"><path fill="#cfcfcf" d="M5 0a5 5 0 0 0-5 5c0 4 5 9 5 9s5-5 5-9a5 5 0 0 0-5-5zm0 7a2 2 0 1 1 0-4 2 2 0 0 1 0 4z"/></svg><span>48 Linden Row, Harbor Vale, FL,<br>Florida, 30000.</span></div>
  <div class="f-item" style="top:175px"><svg width="12" height="12" viewBox="0 0 24 24"><path fill="#cfcfcf" d="M6.6 10.8a15.1 15.1 0 0 0 6.6 6.6l2.2-2.2c.3-.3.7-.4 1-.2 1.1.4 2.3.6 3.6.6.6 0 1 .4 1 1V20c0 .6-.4 1-1 1A17 17 0 0 1 3 4c0-.6.4-1 1-1h3.5c.6 0 1 .4 1 1 0 1.3.2 2.5.6 3.6.1.3 0 .7-.2 1z"/></svg><span>+0100 555 0199</span></div>
  <div class="f-item" style="top:209px"><svg width="13" height="10" viewBox="0 0 13 10"><rect width="13" height="10" fill="#cfcfcf"/><path d="M0 0l6.5 5L13 0" stroke="#141210" fill="none"/></svg><span>hello@copperline.example</span></div>
  <div class="social">chatterbook</div>

  <h4 style="left:483px;width:240px">Quick Contact</h4>
  <div class="field" style="top:112px">Name</div>
  <div class="field" style="top:157px">Email</div>
  <div class="field" style="top:204px;height:62px">Message</div>
  <div class="btn send">SEND</div>

  <h4 style="left:845px;width:268px">Quick Links</h4>
  <ul class="links"><li>Home</li><li>About</li><li>Features</li><li>Services</li><li>Events</li><li>Contact us</li></ul>

  <div class="copy-line"></div>
  <p class="copy">Copyright &copy; 2017. Copperline Collective. All rights reserved.</p>
</footer>

</body>
</html>
```